Brightfen Business Card Redesign & Logo Update

We need to update our business cards to something more modern and fresh. Brightfen can provide the current color schemes and old design examples, but welcome creativity in helping us with this redesign. PLEASE NOTE that we no longer utilize the "tree" and/or "leaf" imagery in our branding. If able would apprecaite an update on the quality of our "words only" logo in Ai. / PNG formats too.

Target Market(s)

Investors, landowners, corporate partners, contractors

Industry/Entity Type

Environmental Restoration & Conservation

Contact Information for Business Card

Logo, persons name, title, mailing address, phone and email, website url

Font styles to use
Other font styles liked:
• Merriweather

Requirements
Nice to have
• Logo, persons name, title, mailing address, phone and email, website url, but open to ideams
Should not have
• No all back backgrounds

```html
<!DOCTYPE html>
<html lang="en">
<head>
<meta charset="utf-8">
<title>Brightfen Business Card</title>
<link href="https://fonts.googleapis.com/css2?family=Merriweather:wght@400;700;900&family=Oswald:wght@500&display=swap" rel="stylesheet">
<style>
  :root {
    --bg: #8e8f92;
    --card-white: #ffffff;
    --card-dark: #2b2b28;
    --ink: #1d1d1d;
    --green: #15853b;
    --orange: #f07a14;
    --rule: #3a3a3a;
    --photo-rock: #4a3a2a;
    --photo-water: #c9cccd;
  }
  * { margin: 0; padding: 0; box-sizing: border-box; }
  html, body { width: 1200px; height: 781px; overflow: hidden; }
  body {
    background: radial-gradient(circle at 50% 40%, #a9aaad, var(--bg));
    font-family: "Merriweather", Georgia, serif;
    position: relative;
  }
  .card {
    position: absolute;
    top: 236px;
    width: 540px;
    height: 309px;
    border-radius: 20px;
    overflow: hidden;
    box-shadow: 0 14px 30px rgba(0,0,0,.28);
  }
  .card--front { left: 40px; background: var(--card-white); }
  .card--back { left: 620px; background: var(--card-dark); }

  .wordmark { position: absolute; }
  .wordmark__name {
    font-family: "Merriweather", Georgia, serif;
    font-weight: 900;
    font-size: 34px;
    letter-spacing: 1px;
    line-height: 1;
    color: var(--green);
  }
  .wordmark__tagline {
    font-family: "Oswald", "Arial Narrow", sans-serif;
    font-weight: 500;
    font-size: 12.5px;
    letter-spacing: .6px;
    margin-top: 6px;
  }
  .card--front .wordmark { left: 34px; top: 84px; }
  .card--front .wordmark__tagline { color: var(--ink); }

  .social { position: absolute; left: 70px; top: 206px; display: flex; gap: 14px; }
  .social__dot { width: 28px; height: 28px; border-radius: 50%; background: var(--green); }
  .social__dot--alt { background: var(--orange); }

  .divider {
    position: absolute; left: 268px; top: 50px;
    width: 1px; height: 170px; background: var(--rule);
  }

  .contact { position: absolute; left: 290px; top: 60px; color: var(--ink); }
  .contact__name { font-weight: 900; font-size: 19px; letter-spacing: .5px; text-transform: uppercase; }
  .contact__title { color: var(--orange); font-size: 12px; margin: 3px 0 10px; }
  .contact__line { font-size: 12px; line-height: 1.6; display: flex; align-items: center; gap: 6px; }
  .contact__line svg { width: 11px; height: 11px; flex: none; }
  .contact__address { font-size: 12px; line-height: 1.55; margin-bottom: 2px; }

  .photo {
    position: absolute; inset: 0;
    background:
      radial-gradient(ellipse 38% 45% at 30% 28%, var(--photo-water), transparent 70%),
      linear-gradient(160deg, var(--photo-rock) 0%, #3b3227 45%, var(--card-dark) 80%);
  }
  .card--back .wordmark { right: 30px; bottom: 34px; text-align: left; }
  .card--back .wordmark__name { color: var(--orange); font-size: 40px; }
  .card--back .wordmark__tagline { color: #ffffff; font-size: 14px; }
</style>
</head>
<body>
  <section class="card card--front" aria-label="Business card front">
    <div class="wordmark">
      <div class="wordmark__name">BRIGHTFEN</div>
      <div class="wordmark__tagline">ENVIRONMENTAL CREDIT COMPANY</div>
    </div>
    <div class="social" aria-label="Social links">
      <span class="social__dot"></span>
      <span class="social__dot social__dot--alt"></span>
      <span class="social__dot"></span>
    </div>
    <div class="divider"></div>
    <div class="contact">
      <div class="contact__name">Mara Ellison</div>
      <div class="contact__title">Director</div>
      <div class="contact__address">4410 Harlow Lane 18,<br>Marlow, TX 75990</div>
      <div class="contact__line">
        <svg viewBox="0 0 12 12"><path d="M2 1h2.5l1 3-1.5 1a7 7 0 0 0 3 3l1-1.5 3 1V10a1 1 0 0 1-1 1A9 9 0 0 1 1 2a1 1 0 0 1 1-1z" fill="#15853b"/></svg>
        (555) 014-2287
      </div>
      <div class="contact__line">
        <svg viewBox="0 0 12 12"><rect x="1" y="2.5" width="10" height="7" fill="#15853b"/><path d="M1 2.5l5 4 5-4" stroke="#fff" fill="none"/></svg>
        info@brightfencredits.com
      </div>
      <div class="contact__line">
        <svg viewBox="0 0 12 12"><circle cx="6" cy="6" r="5" fill="none" stroke="#15853b" stroke-width="1.3"/><path d="M1 6h10M6 1c-2.5 3-2.5 7 0 10M6 1c2.5 3 2.5 7 0 10" stroke="#15853b" fill="none"/></svg>
        www.brightfencredits.com
      </div>
    </div>
  </section>

  <section class="card card--back" aria-label="Business card back">
    <div class="photo" role="img" aria-label="Long-exposure photo of a waterfall flowing over mossy rocks with autumn leaves"></div>
    <div class="wordmark">
      <div class="wordmark__name">BRIGHTFEN</div>
      <div class="wordmark__tagline">ENVIRONMENTAL CREDIT COMPANY</div>
    </div>
  </section>
</body>
</html>
```